Cat-products company needs smart, yet endearing, business card

We need a business card design for a new, but up-and-running, business based in Honolulu, Hawaii. The business is Purrnest Nook Co. Our first product is the most environmentally-friendly cat grass kit ever seen on the planet. Future products, currently in the R&D phase, will include a variety of exciting cat scratchers. We also do consulting work to help apartment-dwellers make their home more cat-friendly and, in the future, plan on doing full, custom installs of structure to create high walkways for cats.

Target Market(s)

Middle-aged, apartment-dwelling, middle-class workers who own 1 or more cats and who dote on them.

Industry/Entity Type

Pet Care

Contact Information for Business Card

A striking, professional, yet warm and friendly design is what we're after.

Font styles to use
Serif
Sans Serif
Other font styles liked:
• Comfortaa

Colors

Designer to choose colors to be used in the design.

Requirements
Must have
• The company logo: (see attachment)
• The company name: Purrnest Nook Co
• The web address: www.purrnestnookco.com
• Email: support@purrnestnookco.com
• Phone: +1 (808) 571 6023
• Update (Fri Jun 30 3017 7:45pm Hawaii Time) I would like, is possible, uploaded picture of the cat grass kit on the back of the card with some text along the lines of: Purrnest Nook Co - Maker Of The Leafiest Feline Sprout Set Yet
Nice to have
• A cat picture, cartoon, real or silhouette that illustrates cats in action and/or relaxing; ie using the apartment space to live, play and relax in and being well-contented.
• Most of the website is done in the font: Comfortaa. It might be nice to continue using this for brand consistency.
Should not have
• Hard-to-read fonts.

```html
<!DOCTYPE html>
<html lang="en">
<head>
<meta charset="utf-8">
<title>Purrnest Nook Co – Business Card</title>
<link rel="stylesheet" href="https://fonts.googleapis.com/css2?family=Comfortaa:wght@400;700&display=swap">
<style>
  :root {
    --page-bg: #efe9e6;
    --pink-edge: #f6a9ab;
    --pink-mid: #f9c2bf;
    --pink-glow: #fde3d8;
    --card-white: #fdf3f1;
    --brown: #4b2327;
    --gold: #f4b018;
    --faint: rgba(255, 255, 255, 0.35);
  }
  * { box-sizing: border-box; margin: 0; padding: 0; }
  html, body { width: 1200px; height: 1015px; overflow: hidden; }
  body {
    background: var(--page-bg);
    font-family: "Comfortaa", sans-serif;
    color: var(--brown);
    position: relative;
  }
  .card {
    position: absolute;
    left: 250px;
    width: 700px;
    height: 400px;
    border-radius: 4px;
    overflow: hidden;
    box-shadow: 0 10px 30px rgba(75, 35, 39, 0.15);
  }
  /* Front */
  .card--front {
    top: 80px;
    background: radial-gradient(circle at 50% 45%, var(--pink-glow) 0%, var(--pink-mid) 38%, var(--pink-edge) 75%);
  }
  .front__art {
    position: absolute;
    left: 215px; top: 35px;
    width: 270px; height: 270px;
    border-radius: 50%;
    background: radial-gradient(circle, rgba(255,230,215,0.8) 0%, rgba(250,200,190,0.4) 70%, rgba(250,200,190,0) 100%);
  }
  .brand {
    position: absolute;
    display: flex; align-items: center; gap: 10px;
    font-weight: 700;
    color: var(--brown);
    white-space: nowrap;
  }
  .brand__dot {
    width: 20px; height: 20px; border-radius: 50%;
    background: var(--gold);
    flex: none;
  }
  .card--front .brand {
    left: 0; right: 0; top: 160px;
    justify-content: center;
    font-size: 38px;
  }
  .front__tagline {
    position: absolute;
    left: 0; right: 0; bottom: 52px;
    text-align: center;
    font-size: 19px;
    letter-spacing: 0.3px;
  }
  /* Back */
  .card--back {
    top: 535px;
    background: linear-gradient(135deg, var(--card-white) 0%, var(--pink-glow) 40%, var(--pink-mid) 75%, var(--pink-edge) 100%);
  }
  .back__art {
    position: absolute;
    left: 360px; top: 70px;
    width: 300px; height: 300px;
    border-radius: 50%;
    background: radial-gradient(circle, var(--faint) 0%, rgba(255,255,255,0.15) 60%, rgba(255,255,255,0) 100%);
  }
  .card--back .brand {
    left: 34px; top: 182px;
    font-size: 24px;
  }
  .back__divider {
    position: absolute;
    left: 318px; top: 85px;
    width: 2px; height: 230px;
    background: var(--brown);
  }
  .contact {
    position: absolute;
    left: 348px; top: 118px;
    list-style: none;
    font-size: 20px;
    line-height: 2.7;
    white-space: nowrap;
  }
</style>
</head>
<body>
  <section class="card card--front" aria-label="Card front">
    <div class="front__art" role="img" aria-label="Faint illustration of a cat's face behind the name"></div>
    <div class="brand"><span class="brand__dot"></span>Purrnest Nook Co</div>
    <p class="front__tagline">Maker Of The Leafiest Feline Sprout Set Yet</p>
  </section>

  <section class="card card--back" aria-label="Card back">
    <div class="back__art" role="img" aria-label="Faint large paw print decoration"></div>
    <div class="brand"><span class="brand__dot"></span>Purrnest Nook Co</div>
    <div class="back__divider"></div>
    <ul class="contact">
      <li>www.purrnestnookco.com</li>
      <li>support@purrnestnookco.com</li>
      <li>+1 (808) 571 6023</li>
    </ul>
  </section>
</body>
</html>
```